Business Card for premium dental clinic

We are a premium dental clinic based in Brasov, Romania with more than 15 year on the market, providing quality dental treatment made by a team of more specialized dentists, working with modern equipment as a solution to beautiful and healthy teeth.

Our current logo for the clinic use 2 square with colors black and gold - dr Ternisu - studio, using family fonts Bodoni, Myriad Pro and Segoe Print.
Depending on the printing we used some gold CMYK background or gold foil picture background or a gold gradient.
We want a business card:
- eye catching business card
- distinguished business card
- premium design
- to keep the color scheme of black and gold
- to attract the customers to spent time reading the information
- modern concept

```html
<!DOCTYPE html>
<html lang="en">
<head>
<meta charset="utf-8">
<title>dr Ternisu studio – business card</title>
<link rel="stylesheet" href="https://fonts.googleapis.com/css2?family=Montserrat:wght@400;500;600&display=swap">
<style>
  :root {
    --stage: #161616;
    --stage-light: #2a2a2a;
    --card: #1e1e1e;
    --card-edge: #262626;
    --gold: #f2cf3a;
    --gold-deep: #c9a227;
    --ink-light: #f1f1f1;
  }
  * { box-sizing: border-box; margin: 0; padding: 0; }
  html, body { width: 1200px; height: 900px; overflow: hidden; }
  body {
    background: radial-gradient(ellipse at 60% 35%, var(--stage-light), var(--stage) 70%);
    font-family: "Montserrat", sans-serif;
    position: relative;
  }
  .card {
    position: absolute;
    left: 250px;
    width: 700px;
    height: 400px;
    background: linear-gradient(160deg, var(--card-edge), var(--card) 60%);
    box-shadow: 0 18px 40px rgba(0,0,0,.55);
  }
  .card--front { top: 34px; }
  .card--back { top: 466px; }

  .brand {
    display: flex;
    align-items: center;
    gap: 14px;
  }
  .brand__square {
    width: 34px;
    height: 34px;
    background: var(--gold);
    flex: none;
  }
  .brand__name {
    font-weight: 500;
    font-size: 30px;
    color: var(--gold);
    letter-spacing: .5px;
    white-space: nowrap;
  }
  .card--front .brand {
    position: absolute;
    left: 50%;
    top: 50%;
    transform: translate(-50%, -50%);
  }
  .card--back .brand {
    position: absolute;
    left: 48px;
    top: 50%;
    transform: translateY(-50%);
  }
  .card--back .brand__name { font-size: 26px; }
  .card--back .brand__square { width: 30px; height: 30px; }

  .divider {
    position: absolute;
    left: 356px;
    top: 100px;
    width: 2px;
    height: 200px;
    background: var(--gold-deep);
  }
  .contact {
    position: absolute;
    left: 388px;
    top: 100px;
    color: var(--ink-light);
  }
  .contact__name {
    font-weight: 600;
    font-size: 30px;
    color: var(--gold);
    letter-spacing: 2px;
    margin-bottom: 10px;
  }
  .contact__line {
    display: flex;
    align-items: center;
    gap: 10px;
    font-size: 18px;
    line-height: 27px;
    letter-spacing: .6px;
  }
  .contact__icon { width: 13px; height: 13px; flex: none; }
  .contact__address {
    margin-top: 10px;
    font-size: 18px;
    line-height: 26px;
    letter-spacing: .8px;
  }
</style>
</head>
<body>

<section class="card card--front" aria-label="Card front">
  <div class="brand">
    <span class="brand__square"></span>
    <span class="brand__name">dr Ternisu studio</span>
  </div>
</section>

<section class="card card--back" aria-label="Card back">
  <div class="brand">
    <span class="brand__square"></span>
    <span class="brand__name">dr Ternisu studio</span>
  </div>

  <div class="divider"></div>

  <div class="contact">
    <p class="contact__name">DR TERNISU</p>
    <p class="contact__line">
      <svg class="contact__icon" viewBox="0 0 16 16" aria-hidden="true">
        <path d="M4 1.5l2.3 3-1.4 1.6c.9 2 2.5 3.6 4.5 4.5l1.6-1.4 3 2.3-1.2 2.6C7 13.6 2.4 9 1.4 2.7z" fill="none" stroke="var(--gold)" stroke-width="1.3" stroke-linejoin="round"/>
      </svg>
      +40 268 555 019
    </p>
    <p class="contact__line">
      <svg class="contact__icon" viewBox="0 0 16 16" aria-hidden="true">
        <rect x="1" y="3" width="14" height="10" fill="none" stroke="var(--gold)" stroke-width="1.3"/>
        <path d="M1 3l7 6 7-6" fill="none" stroke="var(--gold)" stroke-width="1.3"/>
      </svg>
      info@drternisu.ro
    </p>
    <p class="contact__line">
      <svg class="contact__icon" viewBox="0 0 16 16" aria-hidden="true">
        <circle cx="8" cy="8" r="6.5" fill="none" stroke="var(--gold)" stroke-width="1.2"/>
        <ellipse cx="8" cy="8" rx="3" ry="6.5" fill="none" stroke="var(--gold)" stroke-width="1.1"/>
        <path d="M1.5 8h13M2.5 4.8h11M2.5 11.2h11" stroke="var(--gold)" stroke-width="1.1"/>
      </svg>
      www.drternisu.ro
    </p>
    <p class="contact__address">Strada Livezii 27,<br>Brașov 500410, Romania</p>
  </div>
</section>

</body>
</html>
```